New Business Card Design Project

Use the flyer uploaded and website www.brightoakbuilders.com for inspiration.
List Our Services on Backside of business cards
Marcus Delling
Harborline Builders Inc.
Licensed General Contractors
858-471-6093

Contact Information for Business Card

Use the flyer uploaded and website www.brightoakbuilders.com for inspiration. List Our Services on Backside of business cards Marcus Delling Harborline Builders Inc. Licensed General Contractors 858-471-6093

```html
<!DOCTYPE html>
<html lang="en">
<head>
<meta charset="utf-8">
<title>Harborline Builders – Business Card</title>
<link href="https://fonts.googleapis.com/css2?family=Montserrat:wght@400;700&display=swap" rel="stylesheet">
<style>
  :root {
    --bg: #1f1f1f;
    --card: #111111;
    --ink: #f2f2f2;
    --ink-soft: #dcdcdc;
    --rule: #d8d8d8;
  }
  * { margin: 0; padding: 0; box-sizing: border-box; }
  html, body { width: 1200px; height: 1059px; overflow: hidden; background: var(--bg); }
  body { position: relative; font-family: 'Montserrat', sans-serif; color: var(--ink); }

  .card {
    position: absolute;
    left: 254px;
    width: 692px;
    height: 392px;
    background: var(--card);
    border-radius: 24px;
    box-shadow: 0 10px 24px rgba(0,0,0,0.55);
  }
  .card--front { top: 88px; }
  .card--back { top: 548px; }

  .brand {
    position: absolute;
    width: 260px;
    text-align: center;
    font-weight: 400;
    font-size: 19px;
    letter-spacing: 1.5px;
    color: var(--ink);
    text-transform: uppercase;
  }
  .brand__dot {
    display: block;
    width: 14px; height: 14px;
    margin: 0 auto 12px;
    background: var(--ink);
  }
  .card--front .brand { left: 61px; top: 158px; }
  .card--back .brand { left: 47px; top: 184px; }

  .divider { position: absolute; width: 1.5px; background: var(--rule); }
  .card--front .divider { left: 325px; top: 114px; height: 151px; }
  .card--back .divider { left: 334px; top: 96px; height: 237px; }

  .person { position: absolute; left: 344px; top: 116px; }
  .person__name { font-weight: 700; font-size: 25px; line-height: 1.1; }
  .person__title { font-weight: 400; font-size: 14px; color: var(--ink-soft); margin-top: 2px; letter-spacing: 0.3px; }

  .contacts { position: absolute; left: 341px; top: 194px; list-style: none; }
  .contacts li { display: flex; align-items: center; height: 26px; font-size: 15px; letter-spacing: 0.3px; }
  .contacts svg { width: 14px; height: 14px; margin-right: 13px; fill: var(--ink); flex: none; }

  .license {
    position: absolute; left: 0; right: 0; top: 329px;
    text-align: center; font-size: 14px; letter-spacing: 0.3px; color: var(--ink-soft);
  }

  .services { position: absolute; left: 360px; top: 92px; }
  .services__heading { font-weight: 700; font-size: 20px; margin-bottom: 8px; }
  .services__list { list-style: none; }
  .services__list li {
    position: relative; padding-left: 12px;
    font-size: 15.5px; line-height: 24.2px; letter-spacing: 0.2px; color: var(--ink-soft);
  }
  .services__list li::before {
    content: ""; position: absolute; left: 0; top: 10px;
    width: 5px; height: 5px; border-radius: 50%; background: var(--ink);
  }
</style>
</head>
<body>

<section class="card card--front">
  <div class="brand"><span class="brand__dot"></span>Harborline Builders</div>
  <div class="divider"></div>
  <div class="person">
    <h1 class="person__name">Marcus Delling</h1>
    <p class="person__title">Managing Director</p>
  </div>
  <ul class="contacts">
    <li>
      <svg viewBox="0 0 24 24" aria-hidden="true"><path d="M2 9c0-3 5-5 10-5s10 2 10 5v2h-5V9c-1-1-3-1.5-5-1.5S8 8 7 9v2H2zM6 12h12l2 9H4zM12 13.5a3 3 0 1 0 0 6 3 3 0 0 0 0-6z"/></svg>
      858-471-6093
    </li>
    <li>
      <svg viewBox="0 0 24 24" aria-hidden="true"><path d="M2 5h20v2l-10 6L2 7zM2 9.5l10 6 10-6V19H2z"/></svg>
      info@brightoakbuilders.com
    </li>
    <li>
      <svg viewBox="0 0 24 24" aria-hidden="true"><path d="M12 2a10 10 0 1 0 0 20 10 10 0 0 0 0-20zm-1 3c1 1 0 2-1 3s-3 0-3 2 2 2 2 4-1 3-1 4c-3-1-5-4-5-6 0-3 3-6 8-7zm4 2c2 1 4 3 4 6-1 0-2-1-3 0s0 3-1 4-2 1-2 0 1-3 0-4-3 0-3-2 3-1 4-2z"/></svg>
      www.brightoakbuilders.com
    </li>
  </ul>
  <p class="license">CLSB Licensed No #2046815</p>
</section>

<section class="card card--back">
  <div class="brand"><span class="brand__dot"></span>Harborline Builders</div>
  <div class="divider"></div>
  <div class="services">
    <h2 class="services__heading">Our Services</h2>
    <ul class="services__list">
      <li>Remodel: Kitchen &amp; Bath</li>
      <li>Painting: Interior &amp; Exterior</li>
      <li>Flooring: Carpet, Vinyl, Wood</li>
      <li>Window &amp; Door Replacement</li>
      <li>Plumbing: Repair &amp; Upgrades</li>
      <li>Energy Efficienct Upgrades</li>
      <li>Deck &amp; Patio construction</li>
      <li>Water &amp; Mold Damage</li>
      <li>Garage Renovation</li>
    </ul>
  </div>
</section>

</body>
</html>
```